Harrowgate Supply and Trade, LLC

Would like an e-commerce website started

coldbrook bearings website is a business that is almost exactly like ours...I like how in the front of the website...their lines flash across the bottom...I have attached our line card to add some of ours

we are tolk certified...I would like that to show...... attached logo

also attached our logo

```html
<!DOCTYPE html>
<html lang="en">
<head>
<meta charset="utf-8">
<title>Harrowgate Supply and Trade, LLC</title>
<link href="https://fonts.googleapis.com/css2?family=Lato:wght@400;700;900&display=swap" rel="stylesheet">
<style>
:root{
  --green:#5e8f2b;
  --green-dark:#4a7a22;
  --green-text:#6b9a2c;
  --yellow:#f8c914;
  --cream:#fdf8e6;
  --ink:#111;
  --body:#6a6a6a;
  --footer:#1e1e1e;
}
*{margin:0;padding:0;box-sizing:border-box}
html,body{width:1200px;height:4713px;overflow:hidden}
body{position:relative;font-family:'Lato',sans-serif;color:var(--ink);background:#fff}
.abs{position:absolute}
.btn{position:absolute;display:flex;align-items:center;justify-content:center;border-radius:22px;font-size:15px;font-weight:700;text-decoration:none}
.btn-yellow{background:var(--yellow);color:#7a5a00}
.btn-green{background:var(--green);color:var(--yellow)}
.topline{top:0;left:0;width:1200px;height:4px;background:var(--green)}
.brand{display:flex;align-items:center;gap:12px}
.brand-mark{width:34px;height:34px;background:var(--green)}
.brand-name{font-family:'Lato',sans-serif;font-weight:700;color:var(--ink);line-height:1.05}
.brand-name .big{display:block;font-size:34px;letter-spacing:1px}
.brand-name .small{display:block;font-size:15px;letter-spacing:1.5px}
.nav a{position:absolute;transform:translateX(-50%);font-size:15px;font-weight:700;color:var(--ink);text-decoration:none;white-space:nowrap}
.hero{top:161px;left:0;width:1200px;height:563px;background:linear-gradient(135deg,#4a3322,#7b5a3c 40%,#5a4330 70%,#2c2018)}
.hero::after{content:"";position:absolute;inset:0;background:rgba(20,14,10,.45)}
.hero-content{position:absolute;inset:0;z-index:1;text-align:center;color:#fff}
.hero h1{position:absolute;top:262px;left:0;width:1200px;font-size:70px;font-weight:900;line-height:92px;top:101px}
.hero p{position:absolute;top:308px;left:190px;width:820px;font-size:18px;line-height:33px}
.section-title{font-weight:900;font-size:44px;text-transform:uppercase}
.about-title{top:838px;left:110px;line-height:60px}
.about-text{left:600px;width:490px;font-size:14.5px;line-height:31px;color:var(--body)}
.photo{position:absolute}
.photo-1{left:112px;top:1057px;width:459px;height:412px;background:linear-gradient(135deg,#1f2a36,#4a5866 45%,#2a3440);z-index:2}
.photo-2{left:236px;top:1269px;width:852px;height:366px;background:linear-gradient(120deg,#7c8a96,#b9c2c8 35%,#2f5aa8 65%,#dfe3e6);box-shadow:0 8px 30px rgba(0,0,0,.2);z-index:1}
.services{top:1743px;left:0;width:1200px;height:1262px;background:var(--cream)}
.center{text-align:center;width:1200px;left:0}
.lead{font-size:18px;line-height:37px;color:#555}
.card{position:absolute;width:309px;height:395px;background:#fff;box-shadow:0 2px 14px rgba(0,0,0,.06);text-align:center}
.card-img{position:absolute;top:0;left:0;width:309px;height:265px}
.card-curve{position:absolute;left:0;top:200px;width:309px;height:66px}
.card h3{position:absolute;top:256px;left:0;width:309px;font-size:20px;font-weight:700;color:var(--green-text)}
.card p{position:absolute;top:292px;left:22px;width:265px;font-size:14px;line-height:26px;color:var(--body)}
.quote-icon{top:3192px;left:567px;width:66px;height:66px;border-radius:50%;background:var(--yellow)}
.testimonial{font-size:15px;line-height:31px;color:#555}
.side-quote{font-size:15px;line-height:31px;color:#cfcfcf;width:300px;overflow:hidden;white-space:nowrap}
.contact{top:3647px;left:0;width:1200px;height:715px;background:linear-gradient(90deg,#44731f,#5a8a2c 50%,#44731f)}
.field{position:absolute;background:#fff;font-size:14px;color:#777;padding:20px 36px}
.footer{top:4362px;left:0;width:1200px;height:351px;background:var(--footer)}
.footer .brand-name{color:#fff}
.footer .brand-mark{background:var(--green)}
.fnav a{position:absolute;transform:translateX(-50%);font-size:15px;font-weight:700;color:#fff;text-decoration:none;white-space:nowrap}
.social{position:absolute;width:34px;height:34px;border-radius:50%;background:var(--yellow)}
</style>
</head>
<body>
<div class="abs topline"></div>

<header>
  <div class="abs brand" style="left:110px;top:38px">
    <span class="brand-mark"></span>
    <span class="brand-name"><span class="big">HARROWGATE</span><span class="small">Supply and Trade, LLC</span></span>
  </div>
  <a class="btn btn-yellow" style="left:735px;top:40px;width:207px;height:42px">Make An Appointment</a>
  <a class="btn btn-green" style="left:958px;top:40px;width:130px;height:42px">Get Started</a>
  <nav class="nav abs" style="left:0;top:104px;width:1200px">
    <a style="left:483px">Home</a>
    <a style="left:602px">About Us</a>
    <a style="left:744px">Our Services</a>
    <a style="left:900px">Testimonials</a>
    <a style="left:1048px">Contact Us</a>
  </nav>
</header>

<section class="abs hero" role="img" aria-label="Warehouse aisle with shelving and stacked cardboard boxes">
  <div class="hero-content">
    <h1>WELCOME TO HARROWGATE<br>SUPPLY AND TRADE</h1>
    <p>I must explain to you how all this mistaken idea of denouncing pleasure and praising pain was born and I will give you a complete account of the system, and expound the actual teachings</p>
    <a class="btn btn-yellow" style="left:424px;top:399px;width:205px;height:41px">Make An Appointment</a>
    <a class="btn btn-green" style="left:647px;top:399px;width:129px;height:41px">Get Started</a>
  </div>
</section>

<section class="about">
  <h2 class="abs section-title about-title">About Harrowgate<br>Supply and Trade</h2>
  <a class="btn btn-green" style="left:110px;top:978px;width:128px;height:41px">Read More</a>
  <p class="abs about-text" style="top:848px">At vero eos et accusamus et iusto odio dignissimos ducimus qui blanditiis praesentium voluptatum deleniti atque corrupti quos dolores et quas molestias excepturi sint occaecati cupiditate non provident, similique sunt in culpa qui officia deserunt mollitia animi, id est laborum et dolorum fuga. Et harum quidem rerum facilis est et expedita distinctio. Nam libero tempore, cum soluta nobis est eligendi</p>
  <p class="abs about-text" style="top:1064px">Temporibus autem quibusdam et aut officiis debitis aut rerum necessitatibus saepe eveniet ut et voluptates repudiandae sint et molestiae non recusandae. Itaque earum rerum hic tenetur a sapiente delectus, ut aut reiciendis voluptatibus maiores alias consequatur aut perferendis doloribus asperiores repellat.</p>
  <div class="photo photo-1" role="img" aria-label="Technician working on machinery in a dim workshop"></div>
  <div class="photo photo-2" role="img" aria-label="Engineers in hard hats inspecting a large industrial part"></div>
</section>

<section class="abs services">
  <h2 class="abs section-title center" style="top:76px">Our Services</h2>
  <p class="abs lead" style="top:148px;left:150px;width:900px;text-align:center">At vero eos et accusamus et iusto odio dignissimos ducimus qui blanditiis praesentium voluptatum deleniti atque corrupti quos dolores et quas molestias excepturi sint occaecati cupiditate non provident, similique su</p>

  <div class="card" style="left:112px;top:260px">
    <div class="card-img" role="img" aria-label="Hand holding a steel ball bearing" style="background:linear-gradient(135deg,#2a2a2a,#9a9a9a 50%,#d9b9a2)"></div>
    <svg class="card-curve" viewBox="0 0 309 66" preserveAspectRatio="none"><path d="M0 66 Q0 8 154 8 Q309 8 309 66 Z" fill="#fff"/></svg>
    <h3>Bearing Pullers</h3>
    <p>At vero eos et accusamus et iusto odio dignissimos ducimus qui blanditiis praes entium voluptatum dele</p>
  </div>
  <div class="card" style="left:446px;top:260px">
    <div class="card-img" role="img" aria-label="Close-up of interlocking metal gears" style="background:linear-gradient(135deg,#1c1c1c,#777 50%,#333)"></div>
    <svg class="card-curve" viewBox="0 0 309 66" preserveAspectRatio="none"><path d="M0 66 Q0 8 154 8 Q309 8 309 66 Z" fill="#fff"/></svg>
    <h3>Belting Plastic</h3>
    <p>At vero eos et accusamus et iusto odio dignissimos ducimus qui blanditiis praes entium voluptatum dele</p>
  </div>
  <div class="card" style="left:779px;top:260px">
    <div class="card-img" role="img" aria-label="Rows of blue storage bin boxes on shelves" style="background:linear-gradient(135deg,#1e3fa8,#3a6ad8 50%,#cfd8ee)"></div>
    <svg class="card-curve" viewBox="0 0 309 66" preserveAspectRatio="none"><path d="M0 66 Q0 8 154 8 Q309 8 309 66 Z" fill="#fff"/></svg>
    <h3>Bin Boxes</h3>
    <p>At vero eos et accusamus et iusto odio dignissimos ducimus qui blanditiis praes entium voluptatum dele</p>
  </div>
  <div class="card" style="left:112px;top:699px">
    <div class="card-img" role="img" aria-label="Factory floor with conveyor lines" style="background:linear-gradient(135deg,#1f3a6a,#8da2b5 50%,#c9a46a)"></div>
    <svg class="card-curve" viewBox="0 0 309 66" preserveAspectRatio="none"><path d="M0 66 Q0 8 154 8 Q309 8 309 66 Z" fill="#fff"/></svg>
    <h3>Conveyor Components</h3>
    <p>At vero eos et accusamus et iusto odio dignissimos ducimus qui blanditiis praes entium voluptatum dele</p>
  </div>
  <div class="card" style="left:446px;top:699px">
    <div class="card-img" role="img" aria-label="Hands assembling a gearbox bearing" style="background:linear-gradient(135deg,#3a3a3a,#8c8c8c 50%,#b89a86)"></div>
    <svg class="card-curve" viewBox="0 0 309 66" preserveAspectRatio="none"><path d="M0 66 Q0 8 154 8 Q309 8 309 66 Z" fill="#fff"/></svg>
    <h3>Bearings</h3>
    <p>At vero eos et accusamus et iusto odio dignissimos ducimus qui blanditiis praes entium voluptatum dele</p>
  </div>
  <div class="card" style="left:779px;top:699px">
    <div class="card-img" role="img" aria-label="Angle grinder throwing sparks" style="background:linear-gradient(135deg,#222,#5a5a5a 50%,#d9843a)"></div>
    <svg class="card-curve" viewBox="0 0 309 66" preserveAspectRatio="none"><path d="M0 66 Q0 8 154 8 Q309 8 309 66 Z" fill="#fff"/></svg>
    <h3>Casters</h3>
    <p>At vero eos et accusamus et iusto odio dignissimos ducimus qui blanditiis praes entium voluptatum dele</p>
  </div>

  <a class="btn btn-green" style="left:466px;top:1136px;width:128px;height:40px">View More</a>
  <a class="btn btn-yellow" style="left:605px;top:1136px;width:128px;height:40px">Contact Us</a>
</section>

<section class="customers">
  <h2 class="abs section-title center" style="top:3090px">Our Happy Customers</h2>
  <div class="abs quote-icon">
    <svg viewBox="0 0 66 66" width="66" height="66"><path d="M20 40v-8c0-6 3-10 9-11v4c-3 1-4 3-4 5h4v10z M36 40v-8c0-6 3-10 9-11v4c-3 1-4 3-4 5h4v10z" fill="#7a8a1a"/></svg>
  </div>
  <p class="abs side-quote" style="top:3279px;left:-190px;text-align:right;direction:rtl">blanditiis praesentium<br>s excepturi sint occaecati<br>sunt mollitia animi, id est<br>est et expedita</p>
  <p class="abs testimonial" style="top:3279px;left:290px;width:620px;text-align:center">At vero eos et accusamus et iusto odio dignissimos ducimus qui blanditiis praesentium voluptatum deleniti atque corrupti quos dolores et quas molestias excepturi sint occaecati cupiditate non provident, similique sunt in culpa qui officia deserunt mollitia animi, id est laborum et dolorum fuga. Et harum quidem rerum facilis est et expedita</p>
  <p class="abs side-quote" style="top:3279px;left:1030px;text-align:left">At vero eos et accusam<br>voluptatum deleniti atqu<br>cupiditate non providen<br>laborum et dolo</p>
  <p class="abs center" style="top:3423px;font-size:14px;font-weight:700">- Daniel Reeve</p>
  <svg class="abs" style="left:568px;top:3453px" width="64" height="12" viewBox="0 0 64 12">
    <g fill="#e6b800"><path id="st" d="M6 0l1.8 4 4.2.4-3.2 2.8 1 4.2L6 9.2 2.2 11.4l1-4.2L0 4.4 4.2 4z"/><use href="#st" x="13"/><use href="#st" x="26"/><use href="#st" x="39"/></g>
    <path d="M58 0l1.8 4 4.2.4-3.2 2.8 1 4.2L58 9.2l-3.8 2.2 1-4.2L52 4.4l4.2-.4z" fill="none" stroke="#e6b800"/>
  </svg>
  <a class="btn btn-green" style="left:466px;top:3519px;width:128px;height:40px">View More</a>
  <a class="btn btn-yellow" style="left:605px;top:3519px;width:128px;height:40px">Contact Us</a>
</section>

<section class="abs contact">
  <h2 class="abs section-title center" style="top:68px;color:#fff">Get In Touch With Us</h2>
  <p class="abs center" style="top:141px;font-size:15px;color:#fff">Give us a call or complete our form below to schedule your free estimate.</p>
  <div class="field" style="left:152px;top:207px;width:431px;height:58px">First Name</div>
  <div class="field" style="left:616px;top:207px;width:432px;height:58px">Last Name</div>
  <div class="field" style="left:152px;top:294px;width:431px;height:59px">Contact Number</div>
  <div class="field" style="left:616px;top:294px;width:432px;height:59px">Email Address</div>
  <div class="field" style="left:152px;top:382px;width:896px;height:178px">Message</div>
  <a class="btn btn-yellow" style="left:532px;top:593px;width:136px;height:42px;color:#5a6a10">Submit Now</a>
</section>

<footer class="abs footer">
  <div class="abs brand" style="left:476px;top:92px">
    <span class="brand-mark"></span>
    <span class="brand-name"><span class="big">HARROWGATE</span><span class="small">Supply and Trade, LLC</span></span>
  </div>
  <nav class="fnav abs" style="left:0;top:200px;width:1200px">
    <a style="left:307px">Home</a>
    <a style="left:426px">About Us</a>
    <a style="left:569px">Our Services</a>
    <a style="left:724px">Testimonials</a>
    <a style="left:872px">Contact Us</a>
  </nav>
  <p class="abs" style="left:287px;top:268px;font-size:13px;color:#fff">(C) Copyright 2024 | All Rights Reserved</p>
  <div class="abs" role="img" aria-label="tolk certification badge" style="left:660px;top:260px;width:105px;height:36px;background:#eef0f6;border-bottom:4px solid #5b3c9a"></div>
  <span class="social" style="left:793px;top:259px"></span>
  <span class="social" style="left:835px;top:259px"></span>
  <span class="social" style="left:877px;top:259px"></span>
</footer>
</body>
</html>
```